Verodex business card

Business card for sustainable investment company called "Verodex". Verodex is an exchange platform selling carbon credits between buyers and sellers. Carbon Credits are an environmental commodity for reducing global carbon emissions.

the card should obviously have our logo and the theme should be sustainability/environment mixed with a trading platform.

Contact Information for Business Card

Logo, Name, Title, Phone, Email

Colors
0054AA
0677BA
7BADD7
CADEEF
E8F1F8
0094D4
00A9DD
6FCCEA
C7EBF8
E9F6FB
00AB8E
00BBA5
67D7C9
C6EFE9
E9F9F6
59FF00
82FF00
B8FF75
E3FFCB
F4FFEA

```html
<!DOCTYPE html>
<html lang="en">
<head>
<meta charset="utf-8">
<title>Verodex Business Card</title>
<link href="https://fonts.googleapis.com/css2?family=Poppins:wght@400;500;600&display=swap" rel="stylesheet">
<style>
  :root {
    --backdrop: #e6e7e9;
    --card: #ffffff;
    --tint-soft: #e9f6fb;
    --tint-faint: #f4fafd;
    --navy: #1d2b47;
    --brand-blue: #0677ba;
    --accent-blue: #1f7fe6;
    --text: #1f2530;
  }
  * { margin: 0; padding: 0; box-sizing: border-box; }
  html, body {
    width: 1200px; height: 900px; overflow: hidden;
    background: var(--backdrop);
    font-family: "Poppins", sans-serif;
  }
  .canvas { position: relative; width: 1200px; height: 900px; }
  .card {
    position: absolute; top: 216px; width: 309px; height: 501px;
    background: var(--card);
  }
  .card--front {
    left: 279px;
    border-radius: 0 70px 0 70px;
    background: linear-gradient(135deg, var(--tint-soft) 0%, var(--tint-faint) 55%, var(--tint-soft) 100%);
  }
  .card--back {
    left: 617px;
    border-radius: 70px 0 70px 0;
  }
  .brand {
    position: absolute; display: flex; align-items: center; gap: 12px;
  }
  .brand__dot {
    width: 36px; height: 36px; border-radius: 50%;
    background: var(--brand-blue);
  }
  .brand__name {
    font-weight: 600; color: var(--navy); letter-spacing: 0.5px;
    line-height: 1;
  }
  .card--front .brand { left: 32px; top: 234px; }
  .card--front .brand__name { font-size: 34px; }
  .card--back .brand { left: 28px; top: 170px; }
  .card--back .brand__name { font-size: 34px; }
  .person { position: absolute; left: 32px; top: 318px; }
  .person__name {
    font-size: 20px; font-weight: 600; color: var(--navy);
    line-height: 1.1; letter-spacing: 0.3px;
  }
  .person__title {
    font-size: 15px; font-weight: 400; color: var(--accent-blue); line-height: 1.2;
  }
  .contacts { position: absolute; left: 32px; top: 370px; list-style: none; }
  .contacts__item {
    display: flex; align-items: center; gap: 6px;
    font-size: 14px; color: var(--text); height: 18px;
  }
  .contacts__icon { width: 12px; height: 12px; flex: none; }
</style>
</head>
<body>
<div class="canvas">
  <section class="card card--front">
    <div class="brand">
      <span class="brand__dot"></span>
      <span class="brand__name">VERODEX</span>
    </div>
  </section>

  <section class="card card--back">
    <div class="brand">
      <span class="brand__dot"></span>
      <span class="brand__name">VERODEX</span>
    </div>

    <div class="person">
      <p class="person__name">DANIEL HARTLEY</p>
      <p class="person__title">Managing Director</p>
    </div>

    <ul class="contacts">
      <li class="contacts__item">
        <svg class="contacts__icon" viewBox="0 0 24 24" fill="#1f7fe6"><path d="M6.6 10.8a15 15 0 0 0 6.6 6.6l2.2-2.2a1 1 0 0 1 1-.25 11.4 11.4 0 0 0 3.6.57 1 1 0 0 1 1 1V20a1 1 0 0 1-1 1A17 17 0 0 1 3 4a1 1 0 0 1 1-1h3.5a1 1 0 0 1 1 1c0 1.25.2 2.45.57 3.57a1 1 0 0 1-.25 1z"/></svg>
        044-555 218 430
      </li>
      <li class="contacts__item">
        <svg class="contacts__icon" viewBox="0 0 24 24" fill="#1f7fe6"><path d="M2 5h20v14H2z"/><path d="M2 5l10 8 10-8" fill="none" stroke="#fff" stroke-width="1.6"/></svg>
        hello@verodexmail.com
      </li>
      <li class="contacts__item">
        <svg class="contacts__icon" viewBox="0 0 24 24" fill="none" stroke="#1f7fe6" stroke-width="2"><circle cx="12" cy="12" r="10"/><path d="M2 12h20M12 2c3 3 3 17 0 20M12 2c-3 3-3 17 0 20"/></svg>
        www.verodexgroup.com
      </li>
    </ul>
  </section>
</div>
</body>
</html>
```